Aunt Roula's Bakery

I am about to create a luxury boutique that specializes in cake baking and cupcake
and ready for parties and special events and order delivery
the logo has already made

Boutique

Email:auntroulasbakery@mailbox-example.net
Instagram: aunt_roula_bakery
Twitter: xxxxxxx
WhatsApp: xxxxxxx

Requirements
Must have
• luxury design

```html
<!DOCTYPE html>
<html lang="en">
<head>
<meta charset="utf-8">
<title>Aunt Roula's Bakery – Business Card</title>
<link rel="stylesheet" href="https://fonts.googleapis.com/css2?family=Arimo:wght@400;700&display=swap">
<style>
  :root {
    --backdrop: #3b3430;
    --card: #1c1c1d;
    --card-back: #161617;
    --frame: #8d8d8f;
    --silver: #c9c9cc;
    --pink: #e9a3b8;
    --white: #f2f2f2;
  }
  * { box-sizing: border-box; margin: 0; padding: 0; }
  html, body { width: 1200px; height: 787px; overflow: hidden; }
  body {
    background: var(--backdrop);
    font-family: "Arimo", Arial, sans-serif;
    position: relative;
  }
  .card {
    position: absolute;
    top: 239px;
    width: 540px;
    height: 309px;
    border-radius: 4px;
    box-shadow: 0 10px 30px rgba(0,0,0,.45);
  }
  /* Back side */
  .card-back { left: 40px; background: var(--card-back); }
  .card-back .brand-mark {
    position: absolute;
    left: 50%; top: 46%;
    transform: translate(-50%, -50%);
    display: flex; flex-direction: column; align-items: center; gap: 14px;
  }
  .card-back .brand-circle {
    width: 70px; height: 70px;
    border: 2px solid var(--silver);
    border-radius: 50%;
  }
  .card-back .brand-name {
    color: var(--silver);
    font-size: 22px; font-weight: 700;
    letter-spacing: .06em;
  }
  .card-back .website {
    position: absolute;
    left: 0; right: 0; bottom: 34px;
    text-align: center;
    color: var(--silver);
    font-size: 12px;
    letter-spacing: .2em;
  }
  /* Front side */
  .card-front { left: 620px; background: var(--card); }
  .card-front .frame {
    position: absolute; inset: 16px;
    border: 1.5px solid var(--frame);
  }
  .card-front .brand {
    position: absolute;
    left: 16px; top: 16px; bottom: 16px; width: 222px;
    display: flex; flex-direction: column; align-items: center; justify-content: center; gap: 12px;
  }
  .card-front .brand-circle {
    width: 40px; height: 40px; border-radius: 50%;
    background: var(--pink);
  }
  .card-front .brand-name {
    color: var(--pink);
    font-size: 19px; font-weight: 700;
    letter-spacing: .04em;
    text-align: center;
    line-height: 1.2;
  }
  .card-front .divider {
    position: absolute;
    left: 244px; top: 100px; height: 110px;
    border-left: 1px solid var(--frame);
  }
  .card-front .contact {
    position: absolute;
    left: 262px; top: 78px;
  }
  .contact .person-name { color: var(--pink); font-size: 18px; font-weight: 700; }
  .contact .person-role { color: var(--white); font-size: 13px; margin-top: 3px; margin-bottom: 14px; }
  .contact-list { list-style: none; }
  .contact-list li {
    display: flex; align-items: center; gap: 7px;
    color: var(--white);
    font-size: 11.5px;
    line-height: 18px;
  }
  .contact-list svg { width: 12px; height: 12px; flex: none; }
</style>
</head>
<body>
  <section class="card card-back" aria-label="Card back">
    <div class="brand-mark">
      <span class="brand-circle"></span>
      <span class="brand-name">Aunt Roula's Bakery</span>
    </div>
    <p class="website">www.auntroula.example</p>
  </section>

  <section class="card card-front" aria-label="Card front">
    <div class="frame"></div>
    <div class="brand">
      <span class="brand-circle"></span>
      <span class="brand-name">Aunt Roula's<br>Bakery</span>
    </div>
    <div class="divider"></div>
    <div class="contact">
      <p class="person-name">Sami Haddad</p>
      <p class="person-role">President</p>
      <ul class="contact-list">
        <li>
          <svg viewBox="0 0 12 12" aria-hidden="true"><path fill="var(--pink)" d="M2.5 1h2l1 2.5-1.3 1a6 6 0 0 0 3.3 3.3l1-1.3L11 7.5v2a1.5 1.5 0 0 1-1.5 1.5A8.5 8.5 0 0 1 1 2.5 1.5 1.5 0 0 1 2.5 1z"/></svg>
          555 0142 7788
        </li>
        <li>
          <svg viewBox="0 0 12 12" aria-hidden="true"><rect x="1" y="2.5" width="10" height="7" fill="var(--pink)"/><path d="M1 2.5 6 6.5 11 2.5" fill="none" stroke="var(--card)" stroke-width="1"/></svg>
          auntroulasbakery
        </li>
        <li>
          <svg viewBox="0 0 12 12" aria-hidden="true"><circle cx="6" cy="6" r="5" fill="var(--pink)"/></svg>
          auntroulasbakery@mailbox-example.net
        </li>
        <li>
          <svg viewBox="0 0 12 12" aria-hidden="true"><rect x="1" y="1" width="10" height="10" fill="none" stroke="var(--pink)" stroke-width="1.4"/></svg>
          aunt_roula_bakery
        </li>
        <li>
          <svg viewBox="0 0 12 12" aria-hidden="true"><circle cx="6" cy="6" r="4.5" fill="none" stroke="var(--pink)" stroke-width="1.4"/></svg>
          auntroulasbakery
        </li>
      </ul>
    </div>
  </section>
</body>
</html>
```